Business card for Crestline Bathrooms

Please design a business card for our bathroom renovation business. You can use my existing logo, but if you have an idea to modernize it, I would like to see it. Please see attached files first. I would like to use the blue and the orange theme. I like the concept of using the shower head in the logo. Please find following a design (or two) that I have been trying to create with my limited resources. That design was for a sign, but I was going to adopt it and use it as a business card as well. I like the concept of the water splash but I don’t think it “flows” nicely together with the logo. Another thought is that maybe creating the logo out of water splash could work and have a dramatic effect (like the water text and the butterfly picture attached with similar background instead of white). If the above doesn’t work I would like to see a modern simplified design. One of the attached files named as the unwanted business card has all the details that I want included in the business card. Please note that it is two sided.
Updates

I am very thankful for the designs that I have received, but they are very similar and only a couple of attempts to do something with the water splash as per my original brief. Modernizing the logo and having it made out of out of water splash with the orange as color accent could work and have a dramatic effect (like the water text and the butterfly picture attached with similar background instead of white). Please do not use the butterfly itself! This is just an example that images can be created out of water splash.

Contact Information for Business Card

all the details are on the unwonted business card file included

Colors
3176b5

Requirements
Nice to have
• Copied from the brief:
• ... maybe creating the logo out of water splash could work and have a dramatic effect (like the water text and the butterfly picture attached with similar background instead of white). Please do not use the butterfly itself!
Should not have
• I am getting designs with a butterfly. The butterfly picture was an example of creating something from a water splash. The butterfly itself has no association with anything other than the concept of creating a logo out of water splash. Sorry, I thought I was clear in the brief.

```html
<!DOCTYPE html>
<html lang="en">
<head>
<meta charset="utf-8">
<title>Crestline Bathrooms – Business Card</title>
<link href="https://fonts.googleapis.com/css2?family=Roboto:wght@400;500&family=Roboto+Condensed:wght@700&display=swap" rel="stylesheet">
<style>
  :root {
    --navy: #003f6b;
    --navy-text: #1c416c;
    --coral: #fe6463;
    --coral-line: #e8776d;
    --card-white: #f7f7f7;
    --grey-text: #555a60;
    --backdrop: #e2e2e2;
    --white: #ffffff;
  }
  * { box-sizing: border-box; margin: 0; padding: 0; }
  html, body { width: 1200px; height: 960px; overflow: hidden; }
  body {
    background: var(--backdrop);
    font-family: "Roboto", Arial, sans-serif;
    position: relative;
  }
  .card {
    position: absolute;
    width: 602px;
    height: 343px;
    border-radius: 18px;
    overflow: hidden;
  }
  .card--front { left: 314px; top: 113px; background: var(--card-white); }
  .card--back { left: 311px; top: 472px; background: var(--coral); }

  .brand {
    position: absolute;
    display: flex;
    align-items: center;
    gap: 10px;
    color: var(--navy-text);
    font-family: "Roboto", Arial, sans-serif;
    font-weight: 500;
    line-height: 1.05;
  }
  .brand__dot {
    width: 16px; height: 16px; border-radius: 50%;
    background: var(--coral-line); flex: none;
  }
  .card--front .brand { left: 62px; top: 112px; font-size: 34px; }
  .card--back .brand { left: 0; right: 0; top: 58px; justify-content: center; font-size: 34px; }
  .card--back .brand__dot { background: var(--white); }
  .brand__name { display: block; }

  .divider {
    position: absolute; left: 288px; top: 75px;
    width: 1px; height: 155px; background: #cfcfcf;
  }
  .contact { position: absolute; left: 318px; top: 82px; }
  .contact__name {
    font-family: "Roboto Condensed", "Arial Narrow", sans-serif;
    font-weight: 700; font-size: 22px; color: var(--navy-text);
    letter-spacing: 0.2px; margin-bottom: 8px;
  }
  .contact__line { font-size: 15px; color: var(--grey-text); line-height: 18px; }
  .contact__list { list-style: none; margin-top: 10px; }
  .contact__list li {
    display: flex; align-items: center; gap: 8px;
    font-size: 15px; color: var(--grey-text); line-height: 19px;
  }
  .contact__list svg { width: 13px; height: 13px; fill: var(--navy-text); flex: none; }

  .wave { position: absolute; left: 0; top: 0; width: 602px; height: 343px; }
  .web {
    position: absolute; right: 50px; top: 292px;
    color: var(--white); font-size: 15px;
  }

  .services {
    position: absolute; left: 0; right: 0; top: 188px;
    list-style: none; text-align: center;
    color: var(--white); font-size: 15px; line-height: 18px; letter-spacing: 0.2px;
  }
  .memberships {
    position: absolute; left: 0; right: 0; top: 276px;
    display: flex; justify-content: center; align-items: center; gap: 16px;
  }
  .badge { background: var(--white); }
  .badge--round { width: 32px; height: 32px; border-radius: 8px; }
  .badge--wide { width: 118px; height: 24px; border-radius: 2px; }
  .memberships__rule { width: 1px; height: 34px; background: var(--white); }
</style>
</head>
<body>

  <section class="card card--front" aria-label="Business card front">
    <div class="brand">
      <span class="brand__dot"></span>
      <span><span class="brand__name">Crestline</span><span class="brand__name">Bathrooms</span></span>
    </div>

    <div class="divider"></div>

    <div class="contact">
      <h1 class="contact__name">DANIEL MARSH</h1>
      <p class="contact__line">PO Box 48</p>
      <p class="contact__line">Hillcrest Vale 2731</p>
      <ul class="contact__list">
        <li><svg viewBox="0 0 24 24"><path d="M6.6 10.8a15.1 15.1 0 0 0 6.6 6.6l2.2-2.2a1 1 0 0 1 1-.25 11.4 11.4 0 0 0 3.6.57 1 1 0 0 1 1 1V20a1 1 0 0 1-1 1A17 17 0 0 1 3 4a1 1 0 0 1 1-1h3.5a1 1 0 0 1 1 1c0 1.25.2 2.45.57 3.57a1 1 0 0 1-.25 1z"/></svg>0400 555 218</li>
        <li><svg viewBox="0 0 24 24"><path d="M7 1h10a2 2 0 0 1 2 2v18a2 2 0 0 1-2 2H7a2 2 0 0 1-2-2V3a2 2 0 0 1 2-2zm0 3v14h10V4zm5 15.5a1.2 1.2 0 1 0 0 2.4 1.2 1.2 0 0 0 0-2.4z"/></svg>5550 1942</li>
        <li><svg viewBox="0 0 24 24"><path d="M2 5h20v14H2zm2 2v.5l8 5 8-5V7zm0 2.9V17h16V9.9l-8 5z"/></svg>daniel@crestlinebathrooms.com.au</li>
      </ul>
    </div>

    <svg class="wave" viewBox="0 0 602 343" aria-hidden="true">
      <path d="M0 283 C70 305 150 330 230 324 C330 316 430 252 602 270 L602 343 L0 343 Z" fill="var(--navy)"/>
      <path d="M0 283 C70 305 150 330 230 324 C330 316 430 252 602 270" fill="none" stroke="var(--coral-line)" stroke-width="3"/>
    </svg>
    <p class="web">crestlinebathrooms.com.au</p>
  </section>

  <section class="card card--back" aria-label="Business card back">
    <div class="brand">
      <span class="brand__dot"></span>
      <span><span class="brand__name">Crestline</span><span class="brand__name">Bathrooms</span></span>
    </div>

    <ul class="services">
      <li>Complete Bathroom Renovations &amp; Remodelling</li>
      <li>Highly Skilled &amp; Qualified Tradespeople</li>
      <li>Professional Service From Concept To Completion</li>
      <li>All Work Guaranteed</li>
    </ul>

    <div class="memberships" aria-label="Industry memberships">
      <span class="badge badge--round" role="img" aria-label="Industry association badge"></span>
      <span class="memberships__rule"></span>
      <span class="badge badge--wide" role="img" aria-label="Builders association badge"></span>
    </div>
  </section>

</body>
</html>
```